Webbanner-Design
Verkauf von Pools und Zubehör
Es soll ein Banner für unseren Shop sein für eine Aktion, dass Holzpools jetzt sofort lieferbar sind Text:
Verschönern Sie doch Ihren Garten: Holzpools sofort lieferbar!
Unseren Shop finden Sie unter www.brunnkarst17.de
Fotos können von unserer Seite www.brunnkarst17-gallery.de verwendet werden
Das angefügte Bild sollte ebenfalls dabei sein. Hintergrund: die Leute sollen wegen Corona zu Hause bleiben und haben Zeit, daher sind unsere sofort lieferbaren Pools jetzt natürlich gut. Ich bin auch für abweichende Texte offen.

```html
<!DOCTYPE html>
<html lang="de">
<head>
<meta charset="utf-8">
<title>Brunnkarst17 – Holzpools sofort lieferbar</title>
<link href="https://fonts.googleapis.com/css2?family=Open+Sans:wght@400;600&family=Montserrat:wght@800;900&display=swap" rel="stylesheet">
<style>
  :root{
    --topbar:#00b5e8;
    --water-a:#0a8fd6;
    --water-b:#35c3f2;
    --page-grey:#eeeeee;
    --white:#ffffff;
    --text:#333333;
    --muted:#555555;
    --line:#dddddd;
    --navy:#0c1a78;
    --box:#0e3d8c;
  }
  *{margin:0;padding:0;box-sizing:border-box}
  html,body{width:1200px;height:1023px;overflow:hidden}
  body{font-family:"Open Sans",Arial,sans-serif;color:var(--text);background:var(--page-grey);position:relative}
  .water{position:absolute;left:0;top:0;width:1200px;height:577px;background:linear-gradient(135deg,var(--water-a),var(--water-b) 50%,var(--water-a))}
  .page{position:absolute;left:99px;top:0;width:1002px;height:1023px;background:var(--white)}
  .topbar{height:32px;background:var(--topbar);display:flex;justify-content:space-around;align-items:center;color:var(--white);font-size:12.5px}
  .topbar span{display:flex;align-items:center;gap:4px}
  .service-links{position:absolute;right:27px;top:43px;font-size:10.5px;display:flex}
  .service-links a{color:var(--text);text-decoration:none;padding:0 5px;border-left:1px solid var(--line)}
  .service-links a:first-child{border-left:none}
  .brand{position:absolute;left:22px;top:88px;display:flex;align-items:center;gap:8px;font-size:26px;font-weight:600;color:#1a4fa8}
  .brand i{width:22px;height:22px;border-radius:50%;background:var(--topbar);display:block}
  .search{position:absolute;left:547px;top:90px;width:222px;height:30px;border:1px solid #ccc;border-radius:3px;display:flex}
  .search span{flex:1;padding:6px 11px;font-size:12.5px;color:#999}
  .search b{width:37px;border-left:1px solid #ccc;background:#f5f5f5;display:flex;align-items:center;justify-content:center}
  .account{position:absolute;left:795px;top:97px;font-size:12.5px}
  .cart{position:absolute;left:905px;top:97px;font-size:12.5px}
  .mainnav{position:absolute;left:0;top:174px;width:100%;height:45px;border-top:2px solid var(--line);border-bottom:2px solid var(--line);display:flex;align-items:center;padding-left:24px;gap:21px;font-size:12.5px;color:var(--muted)}
  .caret::after{content:"";display:inline-block;margin-left:3px;border:3.5px solid transparent;border-top-color:var(--muted);vertical-align:-1px}
  .banner{position:absolute;left:20px;top:241px;width:961px;height:324px}
  .dots{position:absolute;left:455px;top:591px;display:flex;gap:16px}
  .dots i{width:7px;height:7px;border-radius:50%;background:#333;display:block;margin-top:1px}
  .dots i.on{width:10px;height:10px;margin-top:0;background:none;border:2px solid #333}
  .divider{position:absolute;left:22px;top:642px;width:957px;border-top:1px solid var(--line)}
  .section-title{position:absolute;left:22px;top:656px;font-size:21px;font-weight:400}
  .categories{position:absolute;left:41px;top:756px;display:flex;gap:65px}
  .category{width:263px;text-align:center;font-size:12.5px}
  .category .photo{height:197px;margin-bottom:42px}
  .holz{background:linear-gradient(180deg,#4d7a3c,#6f8a4c 45%,#b08a57 75%,#5e8a3a)}
  .cover{background:linear-gradient(90deg,#6f9a4f,#9a9a98 15%,#1e95e6 25%,#1e95e6 75%,#9a9a98 85%,#6f9a4f)}
  .roll{background:linear-gradient(160deg,#2f4a2a,#b9c9d6 40%,#2a7fe0 65%,#9a9590)}
</style>
</head>
<body>
<div class="water" role="img" aria-label="Hintergrundfoto: bewegte Wasseroberfläche eines Pools"></div>
<div class="page">
  <div class="topbar">
    <span><svg width="11" height="11" viewBox="0 0 24 24"><path fill="#fff" d="M6.6 10.8a15 15 0 006.6 6.6l2.2-2.2a1 1 0 011-.25 11.4 11.4 0 003.6.57 1 1 0 011 1V20a1 1 0 01-1 1A17 17 0 013 4a1 1 0 011-1h3.5a1 1 0 011 1c0 1.25.2 2.45.57 3.57a1 1 0 01-.25 1z"/></svg>+49 (0) 7041 / 318 607 2</span>
    <span><svg width="12" height="12" viewBox="0 0 12 12"><rect width="12" height="12" rx="2" fill="#fff"/><path d="M3 6l2 2 4-4" stroke="#00b5e8" stroke-width="1.8" fill="none"/></svg>persönliche Beratung</span>
    <span><svg width="12" height="12" viewBox="0 0 12 12"><rect width="12" height="12" rx="2" fill="#fff"/><path d="M3 6l2 2 4-4" stroke="#00b5e8" stroke-width="1.8" fill="none"/></svg>sicher Einkaufen</span>
    <span><svg width="12" height="12" viewBox="0 0 12 12"><circle cx="6" cy="6" r="6" fill="#fff"/><path d="M3 6h5M6 3.5L8.5 6 6 8.5" stroke="#00b5e8" stroke-width="1.6" fill="none"/></svg>Brunnkarst-Galerie</span>
  </div>
  <nav class="service-links">
    <a>Startseite</a><a>Mein Konto</a><a>Kontakt</a><a>Unsere Partner</a><a>Bildergalerie</a><a>Wir über uns</a><a>News</a>
  </nav>
  <div class="brand"><i></i>Brunnkarst17</div>
  <div class="search"><span>Suchen</span><b><svg width="15" height="15" viewBox="0 0 16 16"><circle cx="6.5" cy="6.5" r="5" stroke="#00a8e0" stroke-width="2.2" fill="none"/><path d="M10.3 10.3L15 15" stroke="#00a8e0" stroke-width="2.4"/></svg></b></div>
  <div class="account caret">&#9679; Anmelden</div>
  <div class="cart caret">&#9636; 0,00 €</div>
  <nav class="mainnav">
    <span>Sonderangebote</span><span class="caret">Pool &amp; Zubehör</span><span class="caret">Sauna</span><span class="caret">Infrarot</span><span>Holzbadewannen</span>
  </nav>

  <svg class="banner" viewBox="0 0 961 324" aria-label="Aktionsbanner Holzpools">
    <defs>
      <linearGradient id="bannerBg" x1="0" y1="0" x2="1" y2="1">
        <stop offset="0" stop-color="#0b9ddf"/><stop offset="1" stop-color="#1ab3ee"/>
      </linearGradient>
      <linearGradient id="poolScene" x1="0" y1="0" x2="0" y2="1">
        <stop offset="0" stop-color="#3f6a34"/><stop offset=".35" stop-color="#6e5c48"/><stop offset=".5" stop-color="#2f8fe0"/><stop offset=".7" stop-color="#a77a48"/><stop offset="1" stop-color="#d1a469"/>
      </linearGradient>
    </defs>
    <rect width="961" height="324" fill="url(#bannerBg)"/>
    <circle cx="20" cy="20" r="110" fill="#1ab2ee" opacity=".45"/>
    <circle cx="470" cy="30" r="70" fill="#2cc0f4" opacity=".4"/>
    <polygon points="485,0 961,0 961,324 560,324" fill="var(--navy)"/>
    <polygon points="515,0 875,0 961,110 961,207 812,324 590,324" fill="url(#poolScene)" role="img" aria-label="Foto: achteckiger Holzpool mit Holzterrasse und Leiter im Garten"/>
    <text font-family="Montserrat, sans-serif" font-weight="800" fill="#fff" font-size="28" letter-spacing="-1">
      <tspan x="49" y="82" textLength="217" lengthAdjust="spacingAndGlyphs">VERSCHÖNERN SIE</tspan>
      <tspan x="49" y="110" textLength="251" lengthAdjust="spacingAndGlyphs">DOCH IHREN GARTEN</tspan>
    </text>
    <text font-family="Montserrat, sans-serif" font-weight="900" fill="var(--navy)" font-size="47" letter-spacing="-2">
      <tspan x="49" y="170" textLength="240" lengthAdjust="spacingAndGlyphs">HOLZPOOLS</tspan>
      <tspan x="49" y="214" textLength="154" lengthAdjust="spacingAndGlyphs">SOFORT</tspan>
      <tspan x="49" y="257" textLength="215" lengthAdjust="spacingAndGlyphs">LIEFERBAR!</tspan>
    </text>
    <rect x="333" y="67" width="190" height="190" fill="var(--box)"/>
  </svg>

  <div class="dots"><i></i><i class="on"></i><i></i><i></i><i></i></div>
  <div class="divider"></div>
  <h2 class="section-title">Unsere TOP-Kategorien</h2>
  <div class="categories">
    <div class="category"><div class="photo holz" role="img" aria-label="Foto: Holzpool mit Terrasse im Garten"></div>Holzpools</div>
    <div class="category"><div class="photo cover" role="img" aria-label="Foto: blaue Poolabdeckung auf gepflastertem Beckenrand"></div>Poolabdeckungen</div>
    <div class="category"><div class="photo roll" role="img" aria-label="Foto: Rollabdeckung über einem Pool am Steinrand"></div>Oberflur</div>
  </div>
</div>
</body>
</html>
```